Website for Plumbing Company, Mr. FlowKettle

I need a 7-page fully HTML-coded website for my plumbing company, Mr. FlowKettle. We specialize in installation, repair, and replacement of both gas and electric water heaters. Although we offer both tankless (on-demand) water heaters and standard (with tank) water heaters, most of our business is related to standard (with tank) water heaters in the USA market.

These are the pages I need:
1. Home page with sections such as About Us, Our Services, Why Choose Us, Testimonials, Location Map (Palm Beach County Florida), Quote Request Form, Join Our Newsletter, Mission Statement, etc.

2. Gas Water Heaters

3. Electric Water Heaters

4. Tankless Water Heaters

5. About Us

6. Contact Us

7. Privacy Policy, Terms & Conditions

Be sure to mention the following points:
1. Same-Day Service
2. Best Price Guarantee
3. 100% Satisfaction Rating
4. 15-Year Warranty on Water Heater & Parts
5. Lifetime Warranty on Workmanship
*All Warranties are Transferrable Upon Home Sale

Once design is selected and finalized, I need the website coded in a standard HTML/CSS and temporarily hosted on your development server so I can see the website functionality that is not observable from screenshots, such as section animations, etc. Once those details are finalized, I will move the source code to my server and complete the project.

Residential Home Owners and Business Owners

Plumbing, Home Services, Remodeling, Construction

0054AA
0677BA
7BADD7
CADEEF
E8F1F8
FFC000
F8CF3A
FAE287
FDF2CF
FEFAEE
EE7325
F08F49
F5BC92
FAE3D3
FDF4ED

• Clean, colorful, and professional

```html
<!DOCTYPE html>
<html lang="en">
<head>
<meta charset="utf-8">
<title>Mr. FlowKettle — Expert Plumbing</title>
<link rel="stylesheet" href="https://fonts.googleapis.com/css2?family=Archivo:wght@500;600;700;800;900&family=Inter:wght@400;500;600;700&display=swap">
<style>
:root{
  --navy:#0c2550;
  --navy-deep:#0a1a3a;
  --navy-mid:#123a78;
  --blue:#2a9fd8;
  --blue-soft:#cadeef;
  --blue-pale:#e8f1f8;
  --red:#e2473c;
  --red-dark:#c93a30;
  --gold:#ffc000;
  --ink:#14213d;
  --muted:#4a5568;
  --white:#ffffff;
}
*{margin:0;padding:0;box-sizing:border-box}
html,body{width:1200px;height:5074px;overflow:hidden}
body{font-family:"Inter",sans-serif;color:var(--ink);background:var(--white);position:relative}
h1,h2,h3,h4,.display{font-family:"Archivo",sans-serif}
.abs{position:absolute}
.photo{position:absolute}
.hex{clip-path:polygon(50% 0,100% 25%,100% 75%,50% 100%,0 75%,0 25%)}
.btn{position:absolute;display:flex;align-items:center;justify-content:space-between;background:var(--red);color:#fff;border-radius:40px;font-weight:600;font-family:"Inter",sans-serif;padding:0 14px 0 38px}
.btn .circ{width:36px;height:36px;border-radius:50%;background:#fff;display:flex;align-items:center;justify-content:center}

/* HERO */
.hero{position:absolute;left:0;top:0;width:1200px;height:610px;background:linear-gradient(135deg,#0b1c3c 0%,#102a55 60%,#0d2249 100%);overflow:hidden}
.hero .band{position:absolute;right:0;bottom:0;width:1200px;height:610px;background:var(--blue);clip-path:polygon(78% 96%,100% 82%,100% 100%,72% 100%)}
.brand-plate{position:absolute;left:72px;top:-40px;width:226px;height:170px;background:#fff;border-radius:0 0 113px 113px;border:5px solid var(--red);border-top:none;display:flex;align-items:center;justify-content:center;gap:8px;padding-top:36px;z-index:3}
.brand-plate .dot{width:16px;height:16px;border-radius:50%;background:var(--blue)}
.brand-plate span{font-family:"Archivo",sans-serif;font-weight:800;font-size:22px;color:var(--navy)}
.topbar{position:absolute;top:18px;left:320px;right:30px;display:flex;align-items:center;color:#d5deea;font-size:11px}
.topbar .item{display:flex;align-items:center;gap:8px;margin-right:40px}
.topbar .phone{margin-left:auto;font-size:20px;font-weight:700;color:#fff;display:flex;align-items:center;gap:10px;margin-right:0}
.nav{position:absolute;top:68px;left:320px;display:flex;align-items:center;gap:26px;color:#fff;font-size:14px;z-index:3}
.nav .active{background:var(--red);padding:7px 18px;border-radius:20px;border:1px solid #fff}
.nav .quote{position:absolute;left:605px;top:-6px;width:245px;height:40px;border:2px solid #fff;border-radius:22px;display:flex;align-items:center;justify-content:space-between;padding:0 8px 0 22px;font-weight:700;font-size:17px}
.nav .quote .c{width:26px;height:26px;border-radius:50%;background:#fff;display:flex;align-items:center;justify-content:center}
.hero h1{position:absolute;left:110px;top:196px;color:#fff;font-size:82px;font-weight:900;line-height:.98;letter-spacing:0;white-space:nowrap;z-index:2}
.hero p{position:absolute;left:112px;top:378px;width:490px;color:#fff;font-size:16.5px;line-height:1.55;font-weight:500;z-index:2}
.hero .btn{left:110px;top:443px;width:214px;height:66px;border:3px solid #fff;font-size:18px;padding:0 10px 0 28px}
.hero-red{position:absolute;left:636px;top:130px;width:420px;height:470px;background:var(--red)}
.hero-photo{left:652px;top:138px;width:400px;height:450px;background:linear-gradient(160deg,#3a5f93,#c9d6e4 55%,#7a8fa8)}

/* ABOUT */
.about{position:absolute;top:610px;left:0;width:1200px;height:710px;background:#fff}
.about-red{left:190px;top:240px;width:440px;height:430px;background:var(--red)}
.about-photo{left:72px;top:52px;width:508px;height:582px;background:linear-gradient(150deg,#e9edf2 20%,#8aa4c6 55%,#1f4f9e)}
.eyebrow{font-family:"Archivo",sans-serif;font-weight:700;color:var(--blue)}
.about .eyebrow{position:absolute;left:702px;top:82px;font-size:31px}
.about h2{position:absolute;left:702px;top:130px;font-size:41px;line-height:1.1;font-weight:800;color:var(--navy-deep)}
.about p{position:absolute;left:702px;top:242px;width:455px;font-size:15.5px;line-height:1.68;color:#3b4658}
.checks{position:absolute;left:702px;top:418px;width:470px;display:grid;grid-template-columns:238px 232px;row-gap:24px}
.check{display:flex;gap:14px;align-items:flex-start;font-size:14.5px;line-height:1.45;color:#2a3446}
.check svg{flex:none;margin-top:2px}
.about .btn{left:702px;top:583px;width:204px;height:64px;font-size:17px}

/* SERVICES */
.services{position:absolute;top:1320px;left:0;width:1200px;height:780px;background:linear-gradient(180deg,#0c1c3c,#14408a 100%);overflow:hidden}
.services .eyebrow{position:absolute;top:132px;width:100%;text-align:center;font-size:31px}
.services h2{position:absolute;top:180px;width:100%;text-align:center;color:#fff;font-size:41px;line-height:1.12;font-weight:800}
.svc{position:absolute;top:323px;width:328px;height:357px}
.svc .img{position:absolute;left:0;top:0;width:328px;height:274px}
.svc .box{position:absolute;left:36px;top:212px;width:256px;height:145px;background:#fff;text-align:center;padding:20px 22px;box-shadow:0 6px 18px rgba(0,0,0,.2)}
.svc h3{font-size:19px;font-weight:700;color:var(--ink);margin-bottom:14px}
.svc p{font-size:13.5px;line-height:1.6;color:#3b4658}
.dots{position:absolute;display:flex;gap:32px}
.dots i{width:13px;height:13px;border-radius:50%;background:#7f92b4;display:block}
.dots i.on{background:#fff}

/* WHY */
.why{position:absolute;top:2100px;left:0;width:1200px;height:625px;background:var(--blue-soft)}
.why h2{position:absolute;top:36px;width:100%;text-align:center;font-size:41px;font-weight:800;color:var(--navy)}
.why-red{left:200px;top:210px;width:350px;height:450px;background:var(--red)}
.why-photo{left:112px;top:90px;width:410px;height:448px;background:linear-gradient(150deg,#1c3e78 10%,#f1f3f6 45%,#9fb0c4)}
.feat{position:absolute;left:690px;display:flex;align-items:center;gap:22px}
.feat h4{font-size:20px;font-weight:700;color:var(--ink);margin-bottom:6px}
.feat p{font-size:13.5px;color:#2e3848}
.stats{position:absolute;left:90px;top:2688px;width:1017px;height:128px;background:#14408a;border-radius:10px;display:flex;color:#fff;box-shadow:0 4px 10px rgba(0,0,0,.15)}
.stat{flex:1;text-align:center;padding-top:16px}
.stat b{display:block;font-family:"Archivo",sans-serif;font-size:44px;font-weight:800}
.stat span{font-size:20px;font-weight:500}

/* TESTIMONIALS */
.tests{position:absolute;top:2830px;left:0;width:1200px;height:395px}
.tests .tag{position:absolute;left:52px;top:90px;font-size:15px;font-weight:700;color:var(--red)}
.tests h2{position:absolute;left:52px;top:112px;font-size:33px;line-height:1.13;font-weight:800;color:var(--navy-deep)}
.tests .score{position:absolute;left:52px;top:232px;font-family:"Archivo",sans-serif;font-size:37px;font-weight:700;color:#222;display:flex;align-items:center;gap:6px}
.tests .link{position:absolute;left:54px;top:286px;font-size:13px;color:var(--navy-mid);text-decoration:underline}
.tcard{position:absolute;top:85px;width:342px;height:222px;background:#fff;border:1px solid #dfe6ef;border-bottom:4px solid #bcd0e6;border-radius:6px;box-shadow:0 4px 14px rgba(15,40,80,.1);text-align:center;padding:70px 24px 0;font-size:15.5px;line-height:1.6;color:#222}
.tcard em{display:block;font-weight:700}
.tcard .stars{position:absolute;bottom:22px;left:0;right:0;color:var(--gold);font-size:22px;letter-spacing:2px}
.tests .dots i{background:#c7ccd4}
.tests .dots i.on{background:#111}

/* MAP */
.map{position:absolute;top:3225px;left:0;width:1200px;height:372px;background:linear-gradient(135deg,#eef1f4,#e3e8ee 50%,#f1f3f6)}

/* QUOTE */
.quote{position:absolute;top:3597px;left:0;width:1200px;height:595px;background:linear-gradient(180deg,#0f2246,#0c1c3c)}
.quote h2{position:absolute;top:40px;width:100%;text-align:center;color:#fff;font-size:41px;font-weight:800}
.field{position:absolute;width:405px}
.field label{display:block;color:#fff;font-size:17px;font-weight:500;margin-bottom:18px}
.field .in{height:36px;background:#fff;border-radius:18px;position:relative}
.quote .btn{left:470px;top:488px;width:262px;height:64px;border:3px solid #fff;font-size:18px;padding:0 12px 0 36px}

/* EMERGENCY */
.help{position:absolute;top:4192px;left:0;width:1200px;height:298px;overflow:hidden}
.help-photo{left:540px;top:0;width:660px;height:298px;background:linear-gradient(120deg,#dfe4ea,#a9b8c9 45%,#5b7796)}
.help-red{position:absolute;left:0;top:0;width:700px;height:298px;background:var(--red);clip-path:polygon(0 0,100% 0,80% 100%,0 100%)}
.help h3{position:absolute;left:0;width:630px;top:82px;text-align:center;color:#fff;font-size:33px;font-weight:800}
.help small{position:absolute;left:0;width:630px;top:130px;text-align:center;color:#fff;font-size:12.5px;font-weight:700}
.help .num{position:absolute;left:0;width:630px;top:152px;text-align:center;color:#fff;font-family:"Archivo",sans-serif;font-size:61px;font-weight:700}

/* NEWSLETTER */
.news{position:absolute;top:4490px;left:0;width:1200px;height:150px;background:#fff}
.news h3{position:absolute;left:95px;top:42px;font-size:33px;font-weight:700;color:var(--red)}
.news small{position:absolute;left:103px;top:88px;font-size:13px;font-weight:700;color:#1a1a1a}
.news .input{position:absolute;left:474px;top:40px;width:405px;height:64px;border:1.5px solid #9eb3cc;border-radius:32px;padding-left:34px;display:flex;align-items:center;font-size:16px;color:#222}
.news .btn{left:902px;top:37px;width:202px;height:62px;font-size:18px;padding:0 10px 0 34px}
.news .btn .circ{background:transparent;border:2px solid #fff}

/* FOOTER */
.footer{position:absolute;top:4640px;left:0;width:1200px;height:434px;background:#0c1c3c;overflow:hidden}
.footer .band{position:absolute;left:0;top:0;width:1200px;height:120px;background:linear-gradient(90deg,#1e6fb8,var(--blue));clip-path:polygon(0 0,100% 0,100% 26%,0 100%)}
.footer .brand{position:absolute;left:60px;top:210px;display:flex;align-items:center;gap:14px}
.footer .brand .dot{width:70px;height:70px;border-radius:50%;background:var(--blue)}
.footer .brand span{font-family:"Archivo",sans-serif;font-size:40px;font-weight:800;color:#fff}
.fcol{position:absolute;top:122px;color:#fff}
.fcol h4{font-family:"Inter",sans-serif;font-size:15px;font-weight:700;margin-bottom:22px}
.fcol ul{list-style:none}
.fcol li{font-size:12.5px;margin-bottom:16px;color:#e3e9f2}
.fcol li::before{content:"•";margin-right:8px}
.fcol .ci{display:flex;gap:14px;font-size:12.5px;color:#e3e9f2;margin-bottom:18px;line-height:1.35}
.footer .copy{position:absolute;left:44px;top:406px;font-size:11px;color:#c9d2de}
.footer .follow{position:absolute;left:880px;top:404px;font-size:15px;font-weight:700;color:#fff}
.social{position:absolute;top:394px;left:976px;display:flex;gap:15px}
.social i{display:block;width:36px;height:36px;border-radius:50%;background:#fff}
.social i:first-child{background:var(--blue)}
</style>
</head>
<body>

<!-- HERO -->
<header class="hero">
  <div class="band"></div>
  <div class="hero-red hex"></div>
  <div class="photo hero-photo hex" role="img" aria-label="Plumbers in caps and uniforms servicing a wall-mounted water heater"></div>
  <div class="brand-plate"><i class="dot"></i><span>Mr. FlowKettle</span></div>
  <div class="topbar">
    <div class="item"><svg width="14" height="16" viewBox="0 0 14 16"><path d="M7 1a5 5 0 0 0-5 5c0 4 5 9 5 9s5-5 5-9a5 5 0 0 0-5-5z" fill="none" stroke="#e2473c" stroke-width="1.6"/><circle cx="7" cy="6" r="1.8" fill="#e2473c"/></svg>48 Harbor Bend Rd, Lake Worth, FL 33460</div>
    <div class="item"><svg width="15" height="15" viewBox="0 0 16 16"><circle cx="8" cy="8" r="6.5" fill="none" stroke="#e2473c" stroke-width="1.6"/><path d="M8 4v4l3 2" stroke="#e2473c" stroke-width="1.6" fill="none"/></svg>Open 24/7 - Emergency Services</div>
    <div class="item phone"><svg width="20" height="20" viewBox="0 0 24 24"><path d="M6 3l3 4-2 2a12 12 0 0 0 8 8l2-2 4 3-2 3C10 21 3 14 3 5z" fill="none" stroke="#e2473c" stroke-width="2"/></svg>+1 (561) 555-0142</div>
  </div>
  <nav class="nav">
    <span class="active">Home</span><span>About</span><span>Services</span><span>Water Heaters ⌄</span><span>Contact Us</span><span>Privacy Policy</span>
    <span class="quote">Request a Quote <span class="c"><svg width="14" height="14" viewBox="0 0 14 14"><path d="M3 11L11 3M5 3h6v6" stroke="#0c2550" stroke-width="2" fill="none"/></svg></span></span>
  </nav>
  <h1>EXPERT<br>PLUMBING.</h1>
  <p>Fast, reliable, and professional plumbing solutions to keep your home and business running smoothly.</p>
  <div class="btn">Lets Talk <span class="circ"><svg width="18" height="18" viewBox="0 0 24 24"><path d="M6 3l3 4-2 2a12 12 0 0 0 8 8l2-2 4 3-2 3C10 21 3 14 3 5z" fill="#e2473c"/></svg></span></div>
</header>

<!-- ABOUT -->
<section class="about">
  <div class="photo about-red hex"></div>
  <div class="photo about-photo hex" role="img" aria-label="Technician in uniform tightening a fitting on a water heater"></div>
  <div class="eyebrow">About Us</div>
  <h2>Delivering Quality<br>Plumbing Solutions</h2>
  <p>We are committed to providing top-tier plumbing services that ensure comfort, safety, and peace of mind. Our licensed technicians use modern tools and proven methods to solve every plumbing issue quickly and efficiently.</p>
  <div class="checks">
    <div class="check"><svg width="24" height="24" viewBox="0 0 24 24"><circle cx="12" cy="12" r="12" fill="#0c2550"/><path d="M7 12l3.5 3.5L17 9" stroke="#fff" stroke-width="2.2" fill="none"/></svg>Certified professional<br>plumbers</div>
    <div class="check"><svg width="24" height="24" viewBox="0 0 24 24"><circle cx="12" cy="12" r="12" fill="#0c2550"/><path d="M7 12l3.5 3.5L17 9" stroke="#fff" stroke-width="2.2" fill="none"/></svg>Fast response &amp;<br>same-day service</div>
    <div class="check"><svg width="24" height="24" viewBox="0 0 24 24"><circle cx="12" cy="12" r="12" fill="#0c2550"/><path d="M7 12l3.5 3.5L17 9" stroke="#fff" stroke-width="2.2" fill="none"/></svg>Affordable &amp;<br>transparent pricing</div>
    <div class="check"><svg width="24" height="24" viewBox="0 0 24 24"><circle cx="12" cy="12" r="12" fill="#0c2550"/><path d="M7 12l3.5 3.5L17 9" stroke="#fff" stroke-width="2.2" fill="none"/></svg>Guaranteed quality<br>workmanship</div>
  </div>
  <div class="btn">Learn More <span class="circ"><svg width="14" height="14" viewBox="0 0 14 14"><path d="M3 11L11 3M5 3h6v6" stroke="#e2473c" stroke-width="2" fill="none"/></svg></span></div>
</section>

<!-- SERVICES -->
<section class="services">
  <svg class="abs" style="left:0;top:0" width="1200" height="120" viewBox="0 0 1200 120"><polygon points="0,0 1200,0 1200,20" fill="#fff"/><polygon points="0,0 1200,20 1200,80 0,115" fill="#2a9fd8"/></svg>
  <div class="eyebrow">Our Services</div>
  <h2>Provides Professional Plumbing<br>Services for Every Need</h2>
  <article class="svc" style="left:50px">
    <div class="img" role="img" aria-label="Technician inspecting a tank water heater" style="background:linear-gradient(150deg,#f2f4f6,#c5ced8 60%,#2c4e86)"></div>
    <div class="box"><h3>Drain Cleaning</h3><p>Clogged drains cleared<br>quickly and safely.</p></div>
  </article>
  <article class="svc" style="left:428px">
    <div class="img" role="img" aria-label="Hands using a red pipe wrench under a sink" style="background:linear-gradient(150deg,#d9dde2,#8d98a6 55%,#3b3f47)"></div>
    <div class="box"><h3>Water Heater Repair</h3><p>Detecting and<br>repairing hidden and<br>visible leaks.</p></div>
  </article>
  <article class="svc" style="left:804px">
    <div class="img" role="img" aria-label="Brass pipe valves being fitted" style="background:linear-gradient(150deg,#eceef1,#c9a46a 50%,#7d8794)"></div>
    <div class="box"><h3>Pipe Leak Repair</h3><p>Fixing and installing all<br>types of water heaters.</p></div>
  </article>
  <div class="dots" style="left:528px;top:749px"><i class="on"></i><i></i><i></i><i></i></div>
</section>

<!-- WHY -->
<section class="why">
  <h2>Why Choose Us</h2>
  <div class="photo why-red hex"></div>
  <div class="photo why-photo hex" role="img" aria-label="Technician adjusting the controls of a white water heater"></div>
  <div class="feat" style="top:130px"><svg width="64" height="66" viewBox="0 0 64 66"><polygon points="32,2 38,10 48,8 50,18 60,22 54,31 58,41 48,44 44,54 34,50 26,56 20,47 10,46 12,36 4,28 12,21 12,11 22,11 26,3" fill="#1b2230"/><path d="M22 48l-6 16 8-4 4 6 4-14M42 48l6 16-8-4-4 6-4-14" fill="#1b2230"/></svg><div><h4>Licensed &amp; Insured</h4><p>Your home and property are protected.</p></div></div>
  <div class="feat" style="top:244px"><svg width="82" height="60" viewBox="0 0 82 60"><rect x="2" y="6" width="48" height="34" rx="3" fill="#1b2230"/><path d="M52 16h16l10 14v12H52z" fill="#1b2230"/><circle cx="18" cy="46" r="8" fill="#1b2230" stroke="#cadeef" stroke-width="3"/><circle cx="64" cy="46" r="8" fill="#1b2230" stroke="#cadeef" stroke-width="3"/><rect x="57" y="20" width="10" height="9" fill="#cadeef"/></svg><div><h4>Fast Same-Day Service</h4><p>Emergency and urgent plumbing available.</p></div></div>
  <div class="feat" style="top:352px"><svg width="70" height="70" viewBox="0 0 70 70"><path d="M35 2l8 6 10-1 3 10 9 5-4 9 4 10-9 4-3 10-10-1-8 6-8-6-10 1-3-10-9-4 4-10-4-9 9-5 3-10 10 1z" fill="#1b2230"/><path d="M23 36l8 8 16-16" stroke="#fff" stroke-width="5" fill="none"/></svg><div><h4>Certified Technicians</h4><p>Trained experts with years of experience.</p></div></div>
  <div class="feat" style="top:472px"><svg width="70" height="70" viewBox="0 0 70 70"><circle cx="35" cy="35" r="33" fill="#1b2230"/><path d="M35 50l-12-12a7 7 0 0 1 12-8 7 7 0 0 1 12 8z" fill="#fff"/></svg><div><h4>100% Satisfaction Guarantee</h4><p>We stand behind every job.</p></div></div>
</section>
<div class="stats">
  <div class="stat"><b>15K+</b><span>Completed Jobs</span></div>
  <div class="stat"><b>250+</b><span>Expert Technicians</span></div>
  <div class="stat"><b>4.9<span style="color:#e2473c;font-size:40px">★</span></b><span>Rated by Customers</span></div>
</div>

<!-- TESTIMONIALS -->
<section class="tests">
  <div class="tag">TESTIMONIALS</div>
  <h2>Trusted Reviews<br>from Homeowners &amp;<br>Businesses</h2>
  <div class="score">4.6 <span style="color:#ffc000">★</span></div>
  <div class="link">Rating Based on Customer Reviews</div>
  <div class="tcard" style="left:445px">“Very professional and quick service. Highly recommended!”<em>— Marcus T.</em><div class="stars">★★★★★</div></div>
  <div class="tcard" style="left:823px">“Affordable pricing and excellent workmanship.”<em>— Elena P.</em><div class="stars">★★★★★</div></div>
  <div class="dots" style="left:550px;top:350px"><i class="on"></i><i></i><i></i></div>
</section>

<!-- MAP -->
<section class="map" role="img" aria-label="Street map of the service area with a location pin"></section>

<!-- QUOTE -->
<section class="quote">
  <h2>Quote Request Form</h2>
  <div class="field" style="left:130px;top:142px"><label>Full Name</label><div class="in"></div></div>
  <div class="field" style="left:689px;top:142px"><label>Email Address</label><div class="in"></div></div>
  <div class="field" style="left:130px;top:250px"><label>Phone</label><div class="in"></div></div>
  <div class="field" style="left:689px;top:250px"><label>Address</label><div class="in"></div></div>
  <div class="field" style="left:130px;top:354px"><label>Service Type</label><div class="in"><svg class="abs" style="right:14px;top:8px" width="16" height="20" viewBox="0 0 16 20"><path d="M3 5l5 4 5-4M3 12l5 4 5-4" stroke="#111" stroke-width="2" fill="none"/></svg></div></div>
  <div class="field" style="left:689px;top:354px"><label>Property Type</label><div class="in"><svg class="abs" style="right:14px;top:28px" width="16" height="12" viewBox="0 0 16 12"><path d="M3 3l5 5 5-5" stroke="#111" stroke-width="2" fill="none"/></svg></div></div>
  <div class="btn">Request A Quote <span class="circ" style="width:30px;height:30px"><svg width="12" height="12" viewBox="0 0 14 14"><path d="M3 11L11 3M5 3h6v6" stroke="#e2473c" stroke-width="2.2" fill="none"/></svg></span></div>
</section>

<!-- EMERGENCY -->
<section class="help">
  <div class="photo help-photo" role="img" aria-label="Smiling plumber working on water heater piping"></div>
  <div class="help-red"></div>
  <h3>Need Help Right Now?</h3>
  <small>Call our Emergency Line for immediate assistance.</small>
  <div class="num">+1 800-555-0178</div>
</section>

<!-- NEWSLETTER -->
<section class="news">
  <h3>Join Our Newsletter</h3>
  <small>Major plumbing &amp; equipment manufacturers.</small>
  <div class="input">Enter your Email</div>
  <div class="btn">Join Now <span class="circ" style="width:30px;height:30px"><svg width="12" height="12" viewBox="0 0 14 14"><path d="M3 11L11 3M5 3h6v6" stroke="#fff" stroke-width="2.2" fill="none"/></svg></span></div>
</section>

<!-- FOOTER -->
<footer class="footer">
  <div class="band"></div>
  <div class="brand"><i class="dot"></i><span>Mr. FlowKettle</span></div>
  <div class="fcol" style="left:503px;top:128px"><h4>Company</h4><ul><li>Home</li><li>About Us</li><li>Services</li><li>Gas Water Heaters</li><li>Electric Water Heaters</li><li>Tankless Water Heaters</li><li>Contact</li></ul></div>
  <div class="fcol" style="left:725px"><h4>Support</h4><ul><li>Help Center</li><li>FAQs</li><li>Terms &amp; Conditions</li><li>Privacy Policy</li></ul></div>
  <div class="fcol" style="left:960px"><h4>Contact us</h4>
    <div class="ci"><svg width="16" height="18" viewBox="0 0 14 16"><path d="M7 1a5 5 0 0 0-5 5c0 4 5 9 5 9s5-5 5-9a5 5 0 0 0-5-5z" fill="none" stroke="#fff" stroke-width="1.4"/><circle cx="7" cy="6" r="1.8" fill="none" stroke="#fff"/></svg><span>48 Harbor Bend Rd<br>Lake Worth, Florida 33460</span></div>
    <div class="ci"><svg width="16" height="14" viewBox="0 0 16 12"><rect x="1" y="1" width="14" height="10" fill="none" stroke="#fff" stroke-width="1.4"/><path d="M1 1l7 6 7-6" stroke="#fff" stroke-width="1.4" fill="none"/></svg><span>hello@mrflowkettle.com</span></div>
    <div class="ci"><svg width="16" height="16" viewBox="0 0 24 24"><path d="M6 3l3 4-2 2a12 12 0 0 0 8 8l2-2 4 3-2 3C10 21 3 14 3 5z" fill="none" stroke="#fff" stroke-width="2"/></svg><span>+1 (561) 555-0142</span></div>
  </div>
  <div class="copy">© 2026 Mr FlowKettle. All Rights Reserved.</div>
  <div class="follow">Follow Us</div>
  <div class="social"><i></i><i></i><i></i><i></i></div>
</footer>

</body>
</html>
```